Corporate Dinner Invite at Corvessa for BRQ

BRQ is hosting a corporate dinner at the VEP Summit and we need an email attachment invite for the event. Please use some images from this site for inspiration: https://www.corvessadining.example/ivyparlor/

Invite Title:
Join us for dinner!

Event Details:
Tuesday, October 24th 2023 at 6:30pm
Corvessa Dining, Ivy Parlor
347 W Marlow Ave, Chicago, IL 60622

Target Market(s)

Corporate Audience

Font styles to use
Script

Colors
0054AA
0677BA
7BADD7
CADEEF
E8F1F8

Requirements
Must have
• BRQ logo, event date / time, event location details, photo(s) from Ivy Parlor

```html
<!DOCTYPE html>
<html lang="en">
<head>
<meta charset="utf-8">
<title>BRQ Dinner Invitation – Corvessa Dining, Ivy Parlor</title>
<link rel="stylesheet" href="https://fonts.googleapis.com/css2?family=Great+Vibes&family=Alegreya:wght@500;700&display=swap">
<style>
  :root {
    --backdrop: #e3e4e6;
    --paper: #ffffff;
    --navy: #0b2f8f;
    --brand-blue: #0054AA;
    --accent-blue: #0677BA;
    --sky: #7BADD7;
    --mist: #CADEEF;
    --gold: #c8a77a;
    --photo-dark: #2a1a10;
    --photo-amber: #b56a22;
    --photo-glow: #e9a24b;
  }
  * { margin: 0; padding: 0; box-sizing: border-box; }
  html, body { width: 1200px; height: 1200px; overflow: hidden; background: var(--backdrop); }
  .canvas { position: relative; width: 1200px; height: 1200px; }

  .invite {
    position: absolute; left: 205px; top: 47px; width: 790px; height: 1106px;
    background: var(--paper); border: 9px solid var(--navy);
    box-shadow: 0 4px 14px rgba(0,0,0,0.18);
    font-family: "Alegreya", Georgia, serif; color: var(--navy);
    overflow: hidden;
  }

  .host-brand {
    position: absolute; left: 0; right: 0; top: 68px;
    display: flex; justify-content: center; align-items: center; gap: 16px;
  }
  .host-brand__square { width: 30px; height: 30px; background: var(--brand-blue); }
  .host-brand__name { font-size: 64px; font-weight: 700; line-height: 1; color: var(--brand-blue); letter-spacing: 2px; }

  .invite-title {
    position: absolute; left: 0; right: 0; top: 215px; text-align: center;
    font-family: "Great Vibes", cursive; font-weight: 400; font-size: 108px; line-height: 1.1;
    color: var(--navy);
  }

  .photo-frame {
    position: absolute; left: 36px; top: 365px; width: 700px; height: 408px;
    border: 2px solid var(--accent-blue); border-radius: 14px; background: var(--paper);
  }
  .photo-frame__image {
    position: absolute; left: 16px; top: 15px; width: 664px; height: 372px; border-radius: 14px;
    background:
      radial-gradient(ellipse 60% 30% at 50% 55%, rgba(233,162,75,0.45), transparent 70%),
      linear-gradient(180deg, var(--photo-dark) 0%, #4a2c16 45%, var(--photo-amber) 75%, #d9d4cc 100%);
  }

  .event-date {
    position: absolute; left: 0; right: 0; top: 800px; text-align: center;
    font-size: 40px; font-weight: 700; line-height: 1;
  }

  .venue-brand {
    position: absolute; left: 0; right: 0; top: 863px;
    display: flex; flex-direction: column; align-items: center; gap: 10px;
  }
  .venue-brand__circle { width: 62px; height: 62px; border: 1.5px solid var(--gold); border-radius: 50%; }
  .venue-brand__name { font-size: 29px; font-weight: 500; letter-spacing: 3px; color: var(--gold); line-height: 1; }

  .venue-details {
    position: absolute; left: 0; right: 0; top: 980px; text-align: center;
    font-size: 30px; font-weight: 700; line-height: 43px;
  }
</style>
</head>
<body>
<div class="canvas">
  <article class="invite">
    <div class="host-brand">
      <span class="host-brand__square"></span>
      <span class="host-brand__name">BRQ</span>
    </div>

    <h1 class="invite-title">Join us for dinner!</h1>

    <div class="photo-frame">
      <div class="photo-frame__image" role="img" aria-label="Photo of a row of assorted cocktails on a marble bar at Ivy Parlor, with warm blurred bottles behind"></div>
    </div>

    <p class="event-date">Tuesday, October 24th 2023 at 6:30pm</p>

    <div class="venue-brand">
      <span class="venue-brand__circle"></span>
      <span class="venue-brand__name">CORVESSA</span>
    </div>

    <p class="venue-details">Corvessa Dining, Ivy Parlor<br>347 W Marlow Ave, Chicago, IL 60622</p>
  </article>
</div>
</body>
</html>
```